Webpages for Vuolahtinen Software Consulting

Needed: Webpage design.
Details:
One page site with good looking fonts and simple modern design. Logo would also be nice.
Page is for Software consulting company called: "Vuolahtinen Software Consulting". Vuolahtinen is my surname.
Pages should tell viewer that the company is reliable and its employees are hard-core professionals.
Company currently has one employee, that's me. So what I do is what this company does. I am software consultant. Basicly that means that I do Java/JavaEE/Web programming as subcontractor.
Here is more detail information about me.
SPECIALTIES
- Enterprise J2EE Application Programming and Architectures,
- Web development and
- Agile development.
I have over a decade of experience on designing and creating Java based web-services and applications to multiple interfaces. I also have plenty of experience about software architectures, design patterns and integration into third party systems. I’ve got good knowledge about agile software development and testing processes and I am experienced ScrumMaster and software project leader.
Target Market(s)
IT Businesses, Coding companies... Anyone who is buying coding as service.
Industry/Entity Type
Software
Look and feel

```html
<!DOCTYPE html>
<html lang="en">
<head>
<meta charset="utf-8">
<title>Vuolahtinen Software Consulting</title>
<link rel="stylesheet" href="https://fonts.googleapis.com/css2?family=Marcellus&family=Arimo:wght@400;700&display=swap">
<style>
:root{
  --ink:#2b2b2b;
  --header:#2e2e2e;
  --header-dark:#1f1f1f;
  --band:#6d6d6d;
  --band-dark:#4a4a4a;
  --page:#e2e2e2;
  --panel:#f1f1f1;
  --panel-line:#c9c9c9;
  --text:#333;
  --muted:#777;
  --white:#fff;
  --circle:#3a3a3a;
  --circle-ring:#9a9a9a;
}
*{box-sizing:border-box;margin:0;padding:0}
html,body{width:764px;height:1200px;overflow:hidden}
body{background:var(--page);font-family:"Arimo",Arial,sans-serif;color:var(--text);font-size:10px;line-height:1.45;position:relative}
.display{font-family:"Marcellus",Georgia,serif;font-weight:400}

/* header */
.site-header{position:absolute;left:0;top:0;width:764px;height:100px;background:linear-gradient(var(--header),var(--header-dark))}
.brand{position:absolute;left:22px;top:16px;color:var(--white);font-size:30px;letter-spacing:1px}
.search{position:absolute;right:26px;top:26px;display:flex}
.search input{width:130px;height:20px;border:1px solid #555;background:#444;color:#bbb;font-size:9px;padding:0 6px;font-family:inherit}
.search button{width:22px;height:20px;border:0;background:#555}
.main-nav{position:absolute;left:140px;top:70px;display:flex}
.main-nav a{color:#ddd;text-decoration:none;font-size:12px;padding:5px 16px;border-right:1px solid #555}
.main-nav a.active{color:var(--white);font-weight:700;border-bottom:2px solid #ccc}

/* hero */
.hero{position:absolute;left:0;top:100px;width:764px;height:222px;background:linear-gradient(#f6f6f6,#d9d9d9);border-bottom:1px solid #bbb}
.hero-photo{position:absolute;left:100px;top:8px;width:200px;height:214px;background:linear-gradient(#cfcfcf,#8d8d8d 70%,#3a3a3a);border-radius:4px}
.hero-title{position:absolute;left:385px;top:30px;font-size:36px;color:#555}
.hero-text{position:absolute;left:390px;top:82px;width:320px;font-size:10px;color:#333}
.badges{position:absolute;left:420px;top:140px;display:flex;gap:34px}
.badge{width:48px;height:48px;border-radius:50%;background:#bdbdbd}
.badge.square{border-radius:6px}
.hero-arrow{position:absolute;top:100px;width:12px;height:22px;background:#666}
.hero-arrow.left{left:6px;clip-path:polygon(100% 0,0 50%,100% 100%)}
.hero-arrow.right{right:6px;clip-path:polygon(0 0,100% 50%,0 100%)}

/* bands */
.band{position:absolute;left:0;width:764px;background:linear-gradient(var(--band),var(--band-dark));color:var(--white)}
.welcome{top:326px;height:26px;text-align:center;font-size:18px;line-height:26px}

/* intro columns */
.intro{position:absolute;top:360px;width:348px;height:326px;background:var(--panel);border:1px solid var(--panel-line)}
.intro.about{left:38px}
.intro.work{left:390px}
.intro h2{font-size:20px;color:#444;text-align:center;padding:8px 0 6px;border-bottom:1px solid var(--panel-line)}
.intro p{padding:8px 12px;font-size:10px;line-height:1.55}
.more{position:absolute;right:8px;bottom:8px;width:54px;height:22px;background:var(--circle);color:var(--white);font-family:"Marcellus",Georgia,serif;font-size:13px;text-align:center;line-height:22px}

/* news */
.news{top:700px;height:56px}
.news h2{position:absolute;left:20px;top:14px;font-size:22px}
.news p{position:absolute;left:200px;top:14px;width:460px;font-size:10px}
.news .more{right:26px;bottom:16px;background:#2a2a2a;font-family:"Arimo",Arial,sans-serif;font-size:9px}

/* services */
.services{position:absolute;top:774px;left:0;width:764px;display:flex;justify-content:center;gap:50px}
.service{width:200px;height:200px;border-radius:50%;background:radial-gradient(#4a4a4a,var(--circle) 70%,#222);border:4px solid #bcbcbd;box-shadow:inset 0 0 0 6px var(--circle),inset 0 0 0 8px var(--circle-ring);display:flex;flex-direction:column;align-items:center;justify-content:center;color:var(--white);text-align:center}
.service h3{font-size:22px;line-height:1.15}
.service svg{margin-top:10px}

/* newsletter */
.newsletter{top:1008px;height:40px}
.newsletter h2{position:absolute;left:20px;top:6px;font-size:22px}
.newsletter input{position:absolute;left:160px;top:11px;width:140px;height:18px;border:0;font-size:8px;padding:0 5px;color:#888;font-family:inherit}
.newsletter .subscribe{position:absolute;left:306px;top:11px;width:76px;height:18px;background:#222;color:#fff;font-size:10px;text-align:center;line-height:18px}
.newsletter .stay{position:absolute;left:480px;top:6px;font-size:22px}
.social{position:absolute;left:620px;top:10px;display:flex;gap:5px}
.social span{width:20px;height:20px;border-radius:50%;background:#d8d8d8}

/* blog & about */
.blog{position:absolute;left:20px;top:1056px;width:470px;height:100px}
.blog h2,.consult h2{font-size:18px;color:#444}
.blog-avatar{position:absolute;left:8px;top:30px;width:50px;height:50px;border-radius:50%;background:linear-gradient(#c9c9c9,#7a7a7a);border:2px solid #fff}
.blog p{position:absolute;left:70px;top:30px;width:390px;font-size:10px}
.blog time{position:absolute;left:360px;top:82px;font-size:9px;color:var(--muted)}
.consult{position:absolute;left:520px;top:1056px;width:230px;height:100px}
.consult .badges{left:10px;top:34px;gap:22px}
.consult .badge{width:40px;height:40px}

/* footer */
.site-footer{position:absolute;left:0;top:1162px;width:764px;height:38px;border-top:1px solid #bbb;text-align:center;font-size:9px;color:#555}
.site-footer nav{padding-top:6px}
.site-footer nav a{color:#555;text-decoration:none;margin:0 10px}
.site-footer small{display:block;margin-top:6px;font-size:8px}
</style>
</head>
<body>

<header class="site-header">
  <div class="brand display">Vuolahtinen</div>
  <form class="search"><input type="text" value="Search"><button type="button" aria-label="Search"></button></form>
  <nav class="main-nav">
    <a class="active" href="#">Home</a><a href="#">About Us</a><a href="#">Projects</a><a href="#">Services</a><a href="#">Contact Us</a><a href="#">Login</a>
  </nav>
</header>

<section class="hero">
  <span class="hero-arrow left"></span>
  <div class="hero-photo" role="img" aria-label="Photo of a consultant holding a Vuolahtinen sign"></div>
  <h1 class="hero-title display">Software Consulting</h1>
  <p class="hero-text">Lorem Ipsum is that it has a more-or-less normal distribution of letters, as opposed to using 'Content here, content here', making it look like readable English.</p>
  <div class="badges">
    <span class="badge"></span><span class="badge square"></span><span class="badge"></span>
  </div>
  <span class="hero-arrow right"></span>
</section>

<div class="band welcome display">Welcome to Our Website</div>

<article class="intro about">
  <h2 class="display">About Me</h2>
  <p>Lorem Ipsum is simply dummy text of the printing and typesetting industry. Lorem Ipsum has been the industry's standard dummy text ever since the 1500s, when an unknown printer took a galley of type and scrambled it to make a type specimen book. It has survived not only five centuries, but also the leap into electronic typesetting, remaining essentially unchanged. It was popularised in the 1960s with the release of Sheetline sheets containing Lorem Ipsum passages, and more recently with desktop publishing software like Quillset Layout including versions of Lorem Ipsum.</p>
  <span class="more">More</span>
</article>

<article class="intro work">
  <h2 class="display">What we do?</h2>
  <p>Lorem Ipsum is simply dummy text of the printing and typesetting industry. Lorem Ipsum has been the industry's standard dummy text ever since the 1500s, when an unknown printer took a galley of type and scrambled it to make a type specimen book. It has survived not only five centuries, but also the leap into electronic typesetting, remaining essentially unchanged. It was popularised in the 1960s with the release of Sheetline sheets containing Lorem Ipsum passages, and more recently with desktop publishing software like Quillset Layout including versions of Lorem Ipsum.</p>
  <span class="more">More</span>
</article>

<section class="band news">
  <h2 class="display">Latest News</h2>
  <p>Lorem Ipsum is that it has a more-or-less normal distribution of letters, as opposed to using 'Content here, content here', making it look like readable English.</p>
  <span class="more">more...</span>
</section>

<section class="services">
  <div class="service">
    <h3 class="display">Web<br>Development</h3>
    <svg width="28" height="28" viewBox="0 0 28 28"><rect x="4" y="4" width="20" height="20" rx="3" fill="#bbb"/></svg>
  </div>
  <div class="service">
    <h3 class="display">Web<br>Design</h3>
    <svg width="28" height="28" viewBox="0 0 28 28"><path d="M6 22 L20 6 L23 9 L9 25 L5 26 Z" fill="#bbb"/></svg>
  </div>
  <div class="service">
    <h3 class="display">Web<br>Services</h3>
    <svg width="28" height="28" viewBox="0 0 28 28"><circle cx="14" cy="14" r="9" fill="none" stroke="#bbb" stroke-width="5" stroke-dasharray="4 3"/><circle cx="14" cy="14" r="3" fill="#bbb"/></svg>
  </div>
</section>

<section class="band newsletter">
  <h2 class="display">News Letter</h2>
  <input type="text" value="Enter your Email Id">
  <span class="subscribe display">Subscribe</span>
  <h2 class="stay display">Stay with Us</h2>
  <div class="social"><span></span><span></span><span></span><span></span><span></span></div>
</section>

<section class="blog">
  <h2 class="display">Blog</h2>
  <div class="blog-avatar" role="img" aria-label="Author portrait"></div>
  <p>Lorem Ipsum is that it has a more-or-less normal distribution of letters, as opposed to using 'Content here, content here', making it look like readable English.</p>
  <time>Nov-29-2011</time>
</section>

<section class="consult">
  <h2 class="display">Consulting About</h2>
  <div class="badges"><span class="badge"></span><span class="badge square"></span><span class="badge"></span></div>
</section>

<footer class="site-footer">
  <nav><a href="#">Home</a><a href="#">About Us</a><a href="#">Projects</a><a href="#">Services</a><a href="#">Contact Us</a><a href="#">Login</a></nav>
  <small>Copyright © 2011 www.vuolahtinen.example</small>
</footer>

</body>
</html>
```